We need a laundry sheet packingbox desgin

-look at our website lindavel.nl to be in line with our house style/collor
We are a perfume seller and would like to offer also wasshingsheets with NO SMELL, so the customers can buy this incombination with our washingperfumes.
-the wassingheets will be neutrale(NO SMELL)
-it will be for the Dutch market
The next points should be on the desgin of the package
-our brand name: LINDAVEL
-product name: WASSTRIPS
-(contains) Bevat: 30 wasstrips
-30 wasstrips = 60 wasbeurten
Please take some inspiration of others sellers & regarding eco friendly symbols etc.:
voltirra.com & plomkens.nl
Backside information will be provided afther we found the right desgin
Please look at attachement pdf open box.
Here you can find the pdf design where you need to customize:
https://fz.qx/t-kR8bNwL2sY

```html
<!DOCTYPE html>
<html lang="nl">
<head>
<meta charset="utf-8">
<title>Lindavel Wasstrips – verpakking zijkant en voorzijde</title>
<link rel="stylesheet" href="https://fonts.googleapis.com/css2?family=Cinzel:wght@500&family=Gloock&family=Poppins:wght@400;700&display=swap">
<style>
  :root {
    --stage: #4a4a4a;
    --ink: #050505;
    --paper: #f3f2ef;
    --gold: #c9962c;
    --gold-light: #e4c06a;
    --spine-gold: #ddb24c;
    --spine-gold-dark: #c99a35;
    --white: #ffffff;
    --grey-shirt: #a9a9a9;
  }
  * { margin: 0; padding: 0; box-sizing: border-box; }
  html, body {
    width: 900px; height: 1200px; overflow: hidden;
    background: var(--stage);
  }

  /* Spine panel */
  .box-spine {
    position: absolute; left: 80px; top: 50px;
    width: 80px; height: 1100px;
    overflow: hidden;
  }
  .box-spine__pattern {
    position: absolute; inset: 0;
    background: linear-gradient(180deg, var(--spine-gold) 0%, var(--spine-gold-dark) 50%, var(--spine-gold) 100%);
  }
  .box-spine__brand {
    position: absolute; left: 0; top: 0; width: 80px; height: 1100px;
    display: flex; align-items: center; justify-content: center;
    writing-mode: vertical-rl;
    font-family: "Cinzel", serif; font-weight: 500;
    font-size: 40px; letter-spacing: 3px;
    color: var(--white);
  }

  /* Front panel */
  .box-front {
    position: absolute; left: 160px; top: 50px;
    width: 660px; height: 1100px;
    background: var(--ink);
    overflow: hidden;
    font-family: "Poppins", sans-serif;
    color: var(--white);
  }
  .box-front__shape { position: absolute; inset: 0; }
  .floral-pattern {
    position: absolute; left: 0; top: 0; width: 660px; height: 600px;
    background: radial-gradient(ellipse at 60% 30%, #f7f5f0 0%, #ebe7de 100%);
    clip-path: path("M0,0 L660,0 L660,600 C620,450 540,360 380,330 C200,300 60,200 0,0 Z");
  }
  .brand {
    position: absolute; left: 200px; top: 195px; width: 260px;
    text-align: center;
    font-family: "Cinzel", serif; font-weight: 500;
    font-size: 30px; letter-spacing: 2px;
    color: var(--gold);
  }
  .specs {
    position: absolute; left: 35px; top: 380px;
    display: flex; gap: 48px; align-items: center;
  }
  .spec { display: flex; align-items: center; gap: 10px; }
  .spec__value { line-height: 1; }
  .spec__number { display: block; font-size: 26px; font-weight: 400; }
  .spec__label { display: block; font-size: 13px; letter-spacing: 0.5px; }
  .product-title {
    position: absolute; left: 30px; top: 450px;
    font-family: "Gloock", serif; font-size: 112px; line-height: 1.1;
    letter-spacing: -1px; color: var(--white);
  }
  .benefits {
    position: absolute; left: 35px; top: 655px;
    list-style: none; font-size: 22px; line-height: 1.4;
    transform: rotate(-2deg); transform-origin: left top;
  }
  .benefits strong { font-weight: 700; }
  .usage-steps {
    position: absolute; left: 40px; top: 800px;
    display: flex; align-items: center; gap: 18px;
  }
  .usage-steps__shirt {
    width: 130px; height: 130px; border-radius: 14px;
  }
  .usage-steps__shirt--worn { background: var(--grey-shirt); }
  .usage-steps__shirt--clean { background: var(--white); }
  .usage-steps__machine {
    width: 120px; height: 130px; border: 3px solid var(--white);
    border-radius: 4px; position: relative;
  }
  .usage-steps__machine::after {
    content: ""; position: absolute; left: 22px; top: 38px;
    width: 70px; height: 70px; border-radius: 50%;
    border: 3px solid var(--white);
  }
</style>
</head>
<body>
<aside class="box-spine">
  <div class="box-spine__pattern" role="img" aria-label="Goudkleurige zijkant met zacht bladerenpatroon"></div>
  <div class="box-spine__brand">LINDAVEL</div>
</aside>

<main class="box-front">
  <svg class="box-front__shape" width="660" height="1100" viewBox="0 0 660 1100" aria-hidden="true">
    <path d="M0,0 C60,200 200,300 380,330 C540,360 620,450 660,600" fill="none" stroke="var(--gold)" stroke-width="10"/>
    <path d="M0,0 C60,200 200,300 380,330 C540,360 620,450 660,600" fill="none" stroke="var(--gold-light)" stroke-width="3" transform="translate(0,-4)"/>
  </svg>
  <div class="floral-pattern" role="img" aria-label="Fijn lichtgoud bladerenpatroon op witte achtergrond"></div>

  <div class="brand">LINDAVEL</div>

  <div class="specs">
    <div class="spec">
      <svg width="62" height="52" viewBox="0 0 62 52" aria-hidden="true">
        <path d="M20,4 L58,4 L42,46 L4,46 Z" fill="var(--white)"/>
        <path d="M24,8 L60,8 L44,50" fill="none" stroke="var(--white)" stroke-width="2"/>
      </svg>
      <span class="spec__value"><span class="spec__number">30</span><span class="spec__label">wasstrip</span></span>
    </div>
    <div class="spec">
      <svg width="56" height="56" viewBox="0 0 56 56" aria-hidden="true">
        <rect x="2" y="2" width="52" height="52" rx="6" fill="var(--white)"/>
        <rect x="5" y="5" width="46" height="46" rx="5" fill="none" stroke="var(--ink)" stroke-width="1.5"/>
        <circle cx="28" cy="28" r="15" fill="none" stroke="var(--ink)" stroke-width="2.5"/>
        <path d="M13,28 Q20,23 28,28 T43,28 A15,15 0 0 1 13,28 Z" fill="var(--ink)"/>
        <circle cx="31" cy="35" r="2" fill="var(--white)"/>
        <circle cx="35" cy="32" r="1.5" fill="var(--white)"/>
        <circle cx="36" cy="37" r="1.2" fill="var(--white)"/>
      </svg>
      <span class="spec__value"><span class="spec__number">60</span><span class="spec__label">wasbeurten</span></span>
    </div>
  </div>

  <h1 class="product-title">Wasstrips</h1>

  <ul class="benefits">
    <li><strong>60 wasbeurten</strong> per verpakking</li>
    <li>100% <strong>Milieuvriendelijk</strong></li>
    <li>Geschikt voor alle wasbehoeften</li>
  </ul>

  <div class="usage-steps">
    <div class="usage-steps__shirt usage-steps__shirt--worn" role="img" aria-label="Vuil grijs T-shirt met vlekken en een wasstrip"></div>
    <svg width="70" height="40" viewBox="0 0 70 40" aria-hidden="true">
      <path d="M4,30 Q30,0 62,24" fill="none" stroke="var(--white)" stroke-width="2"/>
      <path d="M54,18 L63,25 L52,28" fill="none" stroke="var(--white)" stroke-width="2"/>
    </svg>
    <div class="usage-steps__machine" role="img" aria-label="Wasmachine"></div>
    <svg width="70" height="40" viewBox="0 0 70 40" aria-hidden="true">
      <path d="M4,24 Q34,32 62,14" fill="none" stroke="var(--white)" stroke-width="2"/>
      <path d="M52,12 L63,14 L58,24" fill="none" stroke="var(--white)" stroke-width="2"/>
    </svg>
    <div class="usage-steps__shirt usage-steps__shirt--clean" role="img" aria-label="Schoon wit T-shirt met glinsteringen"></div>
  </div>
</main>
</body>
</html>
```